Budget Brand Responsive Website

Flat vector style website needed for value based IT support company. looking for clean, illustration intensive based design. Current test site can be found at www.bright-mend.co.uk and holding page it www.brightmend.co.uk this will show text and services, please feel free to use placeholder text if you think we need alternative text in places. Emphasis should be on low cost support and services listed on the site, would be nice to see costs in bold images. important colors are the blue, orange and white, see holding page and attached image of an advert

It Company

```html
<!DOCTYPE html>
<html lang="en">
<head>
<meta charset="utf-8">
<title>Bright Mend – IT Support</title>
<link href="https://fonts.googleapis.com/css2?family=Roboto:wght@300;400;500;700;900&display=swap" rel="stylesheet">
<style>
:root{
  --orange:#f15a22;
  --ink:#2a2a2a;
  --charcoal:#1f1f1f;
  --grey:#6b6b6b;
  --light:#f2f2f2;
  --line:#dcdcdc;
  --white:#ffffff;
  --green:#5cb85c;
  --blue:#3a87c8;
  --coral:#ef6b4a;
  --red:#d9363e;
  --teal:#18a6a0;
}
*{box-sizing:border-box;margin:0;padding:0}
html,body{width:1200px;height:3312px;overflow:hidden}
body{font-family:"Roboto",Arial,sans-serif;color:var(--ink);background:var(--white);position:relative}
section,header,footer{position:relative;width:1200px;overflow:hidden}

/* header */
.site-header{height:44px;background:var(--white);display:flex;align-items:center;justify-content:space-between;padding:0 60px;border-bottom:1px solid var(--line)}
.brand{display:flex;align-items:center;gap:8px;font-weight:900;font-size:22px;color:var(--orange);letter-spacing:.5px}
.brand-dot{width:14px;height:14px;border-radius:50%;background:var(--orange)}
.main-nav{display:flex;height:44px}
.main-nav a{display:flex;align-items:center;padding:0 22px;font-size:11px;font-weight:500;color:var(--ink);text-decoration:none;letter-spacing:1px}
.main-nav a.active{background:var(--orange);color:var(--white)}

/* hero */
.hero{height:428px}
.hero-photo{position:absolute;inset:0;background:linear-gradient(100deg,#0f2a44 0%,#1d4e78 35%,#3a3530 65%,#1d1a18 100%)}
.hero-shade{position:absolute;inset:0;background:linear-gradient(90deg,rgba(0,0,0,0) 45%,rgba(0,0,0,.45) 70%)}
.hero-copy{position:absolute;left:620px;top:96px;color:var(--white)}
.hero-copy h1{font-size:34px;font-weight:700;line-height:1.15;width:360px;letter-spacing:.5px}
.hero-list{list-style:none;margin-top:22px}
.hero-list li{display:flex;align-items:center;gap:12px;font-size:13px;margin-bottom:12px}
.tick{width:18px;height:18px;background:var(--teal);display:flex;align-items:center;justify-content:center}
.btn-ghost{display:inline-block;margin:16px 0 0 110px;padding:10px 30px;border:2px solid var(--white);color:var(--white);font-size:12px;font-weight:500}
.slider-dots{position:absolute;left:0;right:0;bottom:22px;display:flex;justify-content:center;gap:10px}
.slider-dots span{width:9px;height:9px;border-radius:50%;background:rgba(255,255,255,.5)}
.slider-dots span.on{background:var(--white)}

/* understand band */
.understand{height:216px;background:var(--orange);color:var(--white);text-align:center;padding-top:54px}
.understand h2{font-size:38px;font-weight:700;letter-spacing:1px}
.understand p{font-size:19px;margin-top:8px}
.understand .call{font-size:21px;font-weight:700;margin-top:6px}

/* who */
.who{height:472px;text-align:center;padding-top:80px}
.boxed-title{display:inline-block;border:2px solid var(--ink);padding:14px 46px;font-size:34px;font-weight:700;letter-spacing:1px}
.who p{width:760px;margin:48px auto 0;font-size:14px;line-height:1.7;color:var(--grey)}
.btn-solid{display:inline-block;background:var(--orange);color:var(--white);padding:13px 42px;font-size:13px;font-weight:500;border-radius:2px}
.who .btn-solid{margin-top:50px}

/* what we do */
.what{height:840px}
.what-bg{position:absolute;inset:0;background:linear-gradient(180deg,#2b2723 0%,#3b332c 50%,#241f1b 100%)}
.what-badge{position:absolute;left:574px;top:52px;width:52px;height:52px;border-radius:50%;background:var(--orange);display:flex;align-items:center;justify-content:center}
.what-title{position:absolute;left:0;right:0;top:122px;text-align:center;color:var(--white);font-size:34px;font-weight:700;letter-spacing:1px}
.what-title:before,.what-title:after{content:"";display:inline-block;width:300px;height:1px;background:rgba(255,255,255,.4);vertical-align:middle;margin:0 24px}
.laptop{position:absolute;left:450px;top:330px;width:300px;height:200px;background:linear-gradient(160deg,#4fa3d9,#1e5f8e);border-radius:8px}
.service{position:absolute;width:320px;color:var(--white)}
.service h3{font-size:15px;font-weight:700;letter-spacing:1px;margin-bottom:8px}
.service li{list-style:none;font-size:12px;line-height:1.8;color:#ddd}
.service .icon{position:absolute;top:12px;width:68px;height:68px;border-radius:50%;background:var(--orange);display:flex;align-items:center;justify-content:center;box-shadow:0 0 0 6px rgba(241,90,34,.25)}
.service.left{left:70px}
.service.left .icon{left:270px}
.service.right{left:820px;padding-left:100px}
.service.right .icon{left:0}
.connector{position:absolute;height:2px;background:rgba(255,255,255,.35)}

/* pricing */
.pricing{height:440px;background:var(--light);text-align:center;padding-top:36px}
.section-title{font-size:32px;font-weight:500;color:var(--ink)}
.section-title:after{content:"";display:block;width:50px;height:3px;background:var(--orange);margin:12px auto 0}
.plans{display:flex;justify-content:center;gap:14px;margin-top:28px}
.plan{width:200px}
.plan-card{background:var(--white);border:1px solid var(--line);height:236px}
.plan-head{height:40px;color:var(--white);font-size:17px;font-weight:500;display:flex;align-items:center;justify-content:center}
.plan.support .plan-head{background:var(--green)}
.plan.voice .plan-head{background:var(--blue)}
.plan.hosting .plan-head{background:var(--coral)}
.plan.cloud .plan-head{background:var(--red)}
.plan-from{font-size:9px;color:var(--orange);margin-top:10px}
.plan-price{font-size:34px;font-weight:700;color:var(--ink);line-height:1.1}
.plan-price small{font-size:13px;font-weight:400;color:var(--grey)}
.plan-tag{font-size:11px;font-weight:700;margin:6px 10px 8px;line-height:1.3;height:28px}
.plan-card ul{list-style:none}
.plan-card li{font-size:10px;color:var(--grey);padding:6px 0;border-top:1px solid var(--line)}
.plan .btn-solid{display:block;margin-top:12px;padding:10px 0;font-size:12px}

/* exceed */
.exceed{height:340px;padding:54px 70px 0;display:flex;gap:70px}
.exceed-copy{width:640px}
.exceed h2,.rating h2{font-size:30px;font-weight:500;color:var(--ink);margin-bottom:24px}
.exceed p{font-size:12px;line-height:1.7;color:var(--grey);margin-bottom:14px}
.rating{width:320px}
.bar{position:relative;height:16px;background:#e6e6e6;margin-bottom:12px}
.bar span{position:absolute;left:0;top:0;bottom:0;background:var(--red);color:var(--white);font-size:9px;line-height:16px;padding-left:8px}

/* reach */
.reach{height:420px;background:var(--orange)}
.reach-map{position:absolute;left:560px;top:40px;width:580px;height:340px;background:radial-gradient(ellipse at center,#c8420d 0%,#e0541b 70%,rgba(241,90,34,0) 100%)}
.reach h2{position:absolute;left:100px;top:40px;color:var(--white);font-size:28px;font-weight:700}
.reach-form{position:absolute;left:100px;top:104px;width:300px}
.field{height:32px;background:var(--white);margin-bottom:12px;font-size:11px;color:#888;padding:9px 10px}
.field.message{height:80px}
.btn-dark{display:inline-block;background:#333;color:var(--white);padding:10px 26px;font-size:12px;margin-top:4px}

/* footer */
.site-footer{height:112px;background:var(--charcoal);color:#ccc}
.footer-cols{display:flex;justify-content:space-between;padding:26px 100px 0}
.footer-cols h4{font-size:12px;font-weight:500;color:var(--white);margin-bottom:4px}
.footer-cols p{font-size:10px;line-height:1.5}
.copyright{position:absolute;left:0;right:0;bottom:10px;text-align:center;font-size:9px;color:#888}
</style>
</head>
<body>

<header class="site-header">
  <div class="brand"><span class="brand-dot"></span>BRIGHT MEND</div>
  <nav class="main-nav">
    <a class="active">HOME</a><a>SUPPORT</a><a>SERVICES</a><a>ABOUT</a><a>CONTACT</a>
  </nav>
</header>

<section class="hero">
  <div class="hero-photo" role="img" aria-label="Flat illustration of a computer monitor with a padlock and devices over a photo of people working at a desk"></div>
  <div class="hero-shade"></div>
  <div class="hero-copy">
    <h1>WE MAKE IT SIMPLE&nbsp; AND FAIRER!</h1>
    <ul class="hero-list">
      <li><span class="tick"><svg width="12" height="12" viewBox="0 0 12 12"><path d="M2 6l3 3 5-6" fill="none" stroke="#fff" stroke-width="2"/></svg></span>Fair Pricing</li>
      <li><span class="tick"><svg width="12" height="12" viewBox="0 0 12 12"><path d="M2 6l3 3 5-6" fill="none" stroke="#fff" stroke-width="2"/></svg></span>No Contracts</li>
      <li><span class="tick"><svg width="12" height="12" viewBox="0 0 12 12"><path d="M2 6l3 3 5-6" fill="none" stroke="#fff" stroke-width="2"/></svg></span>Fast Response</li>
      <li><span class="tick"><svg width="12" height="12" viewBox="0 0 12 12"><path d="M2 6l3 3 5-6" fill="none" stroke="#fff" stroke-width="2"/></svg></span>Latest Technology</li>
      <li><span class="tick"><svg width="12" height="12" viewBox="0 0 12 12"><path d="M2 6l3 3 5-6" fill="none" stroke="#fff" stroke-width="2"/></svg></span>Satisfied Customers</li>
    </ul>
    <span class="btn-ghost">Know More</span>
  </div>
  <div class="slider-dots"><span class="on"></span><span></span><span></span><span></span><span></span></div>
</section>

<section class="understand">
  <h2>WE UNDERSTAND</h2>
  <p>the Client need and satisfy them</p>
  <p class="call">Call us today on 01632 960 222</p>
</section>

<section class="who">
  <h2 class="boxed-title">WHO WE ARE?</h2>
  <p>Bright Mend is a market leading Managed Service Provider (MSP). With years of industry experience, our commitment to delivering leading technologies combined with a focus on quality service delivery has been one of the critical success factors to our continued and healthy growth.</p>
  <span class="btn-solid">Know More</span>
</section>

<section class="what">
  <div class="what-bg" role="img" aria-label="Dark wooden desk background photo"></div>
  <div class="what-badge"><svg width="24" height="24" viewBox="0 0 24 24"><path d="M12 3l2.5 6H21l-5 4 2 7-6-4-6 4 2-7-5-4h6.5z" fill="#fff"/></svg></div>
  <h2 class="what-title">WHAT WE DO</h2>
  <div class="laptop" role="img" aria-label="Flat illustration of a laptop surrounded by cloud and network icons"></div>
  <div class="connector" style="left:410px;top:380px;width:40px"></div>
  <div class="connector" style="left:750px;top:380px;width:40px"></div>
  <div class="connector" style="left:410px;top:480px;width:40px"></div>
  <div class="connector" style="left:750px;top:480px;width:40px"></div>

  <div class="service left" style="top:210px">
    <h3>SECURITY</h3>
    <ul><li>Encryption</li><li>Antivirus &amp; Anti Malware</li><li>Patch Management Solutions</li></ul>
    <span class="icon"><svg width="30" height="30" viewBox="0 0 30 30"><rect x="7" y="13" width="16" height="13" rx="2" fill="#fff"/><path d="M10 13V9a5 5 0 0 1 10 0v4" fill="none" stroke="#fff" stroke-width="3"/></svg></span>
  </div>
  <div class="service left" style="top:410px">
    <h3>HOSTING</h3>
    <ul><li>Hosted Mail Server</li><li>Office Suite Plus</li><li>Email Protection</li></ul>
    <span class="icon"><svg width="30" height="30" viewBox="0 0 30 30"><rect x="6" y="6" width="18" height="7" rx="1" fill="#fff"/><rect x="6" y="17" width="18" height="7" rx="1" fill="#fff"/><circle cx="20" cy="9.5" r="1.5" fill="#f15a22"/><circle cx="20" cy="20.5" r="1.5" fill="#f15a22"/></svg></span>
  </div>
  <div class="service left" style="top:610px">
    <h3>CLOUD</h3>
    <ul><li>Backup and DR</li><li>Virtual Desktops</li><li>Virtual Private Servers</li></ul>
    <span class="icon"><svg width="32" height="32" viewBox="0 0 32 32"><path d="M9 24a6 6 0 0 1 0-12 8 8 0 0 1 15 2 5 5 0 0 1-1 10z" fill="#fff"/></svg></span>
  </div>

  <div class="service right" style="top:210px">
    <h3>SUPPORT</h3>
    <ul><li>Unlimited Remote Support</li><li>Monitoring, Auditing &amp; more</li><li>24 hours 7 days a week</li></ul>
    <span class="icon"><svg width="30" height="30" viewBox="0 0 30 30"><path d="M6 18v-3a9 9 0 0 1 18 0v3" fill="none" stroke="#fff" stroke-width="3"/><rect x="4" y="16" width="6" height="9" rx="2" fill="#fff"/><rect x="20" y="16" width="6" height="9" rx="2" fill="#fff"/></svg></span>
  </div>
  <div class="service right" style="top:410px">
    <h3>VOICE</h3>
    <ul><li>VoIP Telephone Systems</li><li>Telephone Lines</li><li>SIP Trunking &amp; more</li></ul>
    <span class="icon"><svg width="30" height="30" viewBox="0 0 30 30"><path d="M8 5l4 1 1 5-3 2a13 13 0 0 0 7 7l2-3 5 1 1 4c-1 2-3 3-5 3C12 25 5 18 5 10c0-2 1-4 3-5z" fill="#fff"/></svg></span>
  </div>
  <div class="service right" style="top:610px">
    <h3>INTERNET</h3>
    <ul><li>Business Broadband</li><li>Leased Lines</li><li>Fibre Broadband</li></ul>
    <span class="icon"><svg width="30" height="30" viewBox="0 0 30 30"><circle cx="15" cy="15" r="10" fill="none" stroke="#fff" stroke-width="2.5"/><ellipse cx="15" cy="15" rx="4.5" ry="10" fill="none" stroke="#fff" stroke-width="2"/><path d="M5 15h20M7 10h16M7 20h16" stroke="#fff" stroke-width="2"/></svg></span>
  </div>
</section>

<section class="pricing">
  <h2 class="section-title">Plan &amp; Pricing</h2>
  <div class="plans">
    <div class="plan support">
      <div class="plan-card">
        <div class="plan-head">Support</div>
        <p class="plan-from">Starts from</p>
        <p class="plan-price">£ 8 <small>/mo</small></p>
        <p class="plan-tag">Unlimited Monthly Remote Support</p>
        <ul><li>Workstations £8 pm</li><li>Cloud AV £2 pm</li><li>Servers £45 pm</li></ul>
      </div>
      <span class="btn-solid">More</span>
    </div>
    <div class="plan voice">
      <div class="plan-card">
        <div class="plan-head">Voice</div>
        <p class="plan-from">Starts from</p>
        <p class="plan-price">£ 45 <small>/mo</small></p>
        <p class="plan-tag">Lower Rates And Call Charges</p>
        <ul><li>PBX from £45 pm</li><li>Line rental from £9 pm</li><li>Phone numbers from £2 pm</li></ul>
      </div>
      <span class="btn-solid">More</span>
    </div>
    <div class="plan hosting">
      <div class="plan-card">
        <div class="plan-head">Hosting</div>
        <p class="plan-from">Starts from</p>
        <p class="plan-price">£ 2 <small>/mo</small></p>
        <p class="plan-tag">Flexible And Secure</p>
        <ul><li>Email hosting from £2 pm</li><li>Email Protection from £1 pm</li><li>Office Suite Plus from £4 pm</li></ul>
      </div>
      <span class="btn-solid">More</span>
    </div>
    <div class="plan cloud">
      <div class="plan-card">
        <div class="plan-head">Cloud</div>
        <p class="plan-from">Starts from</p>
        <p class="plan-price">£ 0 <small>/mo</small></p>
        <p class="plan-tag">Reduce Costs &amp; Increase Performance</p>
        <ul><li>Online Backup</li><li>Private Cloud Servers</li><li>Virtual Desktop</li></ul>
      </div>
      <span class="btn-solid">More</span>
    </div>
  </div>
</section>

<section class="exceed">
  <div class="exceed-copy">
    <h2>We Exceed Expectation</h2>
    <p>Unlike traditional IT support companies and other managed service providers, we do not base our success rate on rigid SLA agreements. We understand that our clients' systems are paramount to their business success, and our responsiveness is directly correlated.</p>
    <p>At Bright Mend we measure our success on customer satisfaction. It is for this reason that we ensure over ninety percent of incoming calls reporting incidents are responded to within twenty minutes and over eighty percent of calls are resolved on first contact.</p>
  </div>
  <div class="rating">
    <h2>Rating</h2>
    <div class="bar"><span style="width:92%">Support 92%</span></div>
    <div class="bar"><span style="width:88%">Value 88%</span></div>
    <div class="bar"><span style="width:80%">Speed 80%</span></div>
    <div class="bar"><span style="width:95%">Service 95%</span></div>
    <div class="bar"><span style="width:75%">Reach 75%</span></div>
  </div>
</section>

<section class="reach">
  <div class="reach-map" role="img" aria-label="Dotted world map"></div>
  <h2>Reach us!</h2>
  <div class="reach-form">
    <div class="field">Name</div>
    <div class="field">Email Address</div>
    <div class="field">Contact Number</div>
    <div class="field message">Message</div>
    <span class="btn-dark">Send</span>
  </div>
</section>

<footer class="site-footer">
  <div class="footer-cols">
    <div><h4>Essex Office</h4><p>sales@brightmend.co.uk</p></div>
    <div><h4>Derby Office</h4><p>info@brightmend.co.uk</p></div>
    <div><h4>Support</h4><p>+44 (0) 1632 960 222</p><p>support@brightmend.co.uk</p></div>
    <div><h4>Sales</h4><p>+44 (0) 1632 960 223</p></div>
  </div>
  <p class="copyright">© Copyright 2017 Bright Mend</p>
</footer>

</body>
</html>
```